UX - Need some screens design for a Skill Assessment Application

I am building an app to carry out skill assessments. Depending on how the assessment is configured, it may have one or more parts
1. Question based assessment (Multiple Choice, True False, Fill in the blanks"
2. Endorsement by two colleagues - A screen that allows user to pick colleagues based on search and shows the status of pending requests
3. A written submission - a page that explains the format of the submission and a file upload
As each assessment can be configured with or without any of the steps, the assessment UI must be such that these areas get hidden/displayed based on configuration.
Colour codes to be used can be #0e78bb and #ffffff
There will also be a start screen (instructions) and an end screen (results)
Target Market(s)
Enterprise software
Number of Pages Required
4 page

```html
<!DOCTYPE html>
<html lang="en">
<head>
<meta charset="utf-8">
<title>Corvantia – Assessments</title>
<link href="https://fonts.googleapis.com/css2?family=Inter:wght@400;500;600&display=swap" rel="stylesheet">
<style>
:root{
  --brand:#0457ae;
  --brand-line:#2a6fbd;
  --stat-card:#1c68bd;
  --stat-icon:#3a7fcb;
  --accent:#0e78bb;
  --accent-btn:#1a7fc6;
  --white:#ffffff;
  --muted-on-blue:#a9cbef;
  --page:#f4f5f7;
  --ink:#1f2328;
  --ink-soft:#4b5057;
  --chip:#e6e8eb;
  --tick:#11998e;
  --photo:#6b7a90;
}
*{box-sizing:border-box;margin:0;padding:0}
html,body{width:1200px;height:771px;overflow:hidden}
body{font-family:'Inter',sans-serif;background:var(--page);color:var(--ink)}
.hero{background:var(--brand);height:288px;color:var(--white)}
.topbar{height:43px;border-bottom:1px solid var(--brand-line);position:relative;display:flex;align-items:center;padding:0 70px}
.brand{display:flex;align-items:center;gap:14px;font-weight:600;font-size:14px}
.brand-dot{width:21px;height:21px;border-radius:50%;background:var(--white)}
.nav{position:absolute;left:488px;top:0;height:43px;display:flex;gap:20px;font-size:12.5px}
.nav a{color:#d4e4f6;text-decoration:none;line-height:43px;position:relative}
.nav a.active{color:var(--white);font-weight:600}
.nav a.active::after{content:"";position:absolute;left:0;right:0;bottom:0;height:3px;background:#37a8e6}
.tools{position:absolute;right:70px;top:8px;display:flex;align-items:center;gap:16px}
.avatar-sm{width:27px;height:27px;border-radius:50%;background:var(--photo);border:2px solid var(--white)}
.welcome{position:relative;height:99px}
.avatar-lg{position:absolute;left:57px;top:28px;width:43px;height:43px;border-radius:50%;background:var(--photo)}
.greet{position:absolute;left:121px;top:31px;font-size:11.5px;color:var(--muted-on-blue)}
.user-name{position:absolute;left:121px;top:49px;font-size:16.5px;font-weight:600}
.create-btn{position:absolute;left:965px;top:32px;width:178px;height:35px;background:var(--accent-btn);border-radius:3px;display:flex;align-items:center;justify-content:center;gap:7px;font-size:11.5px;font-weight:500}
.summary-label{margin-left:57px;font-size:13px;font-weight:500}
.stats{display:flex;gap:16px;margin:11px 57px 0}
.stat{width:260px;height:89px;background:var(--stat-card);border-radius:3px;position:relative}
.stat-icon{position:absolute;left:14px;top:14px;width:34px;height:34px;background:var(--stat-icon);border-radius:2px;display:flex;align-items:center;justify-content:center}
.stat-num{position:absolute;left:65px;top:20px;font-size:17px;font-weight:600}
.stat-title{position:absolute;left:65px;top:47px;font-size:12px;font-weight:500}
.stat-sub{position:absolute;left:65px;top:65px;font-size:9.5px;color:#c9ddf3}
.main{padding:0 71px;position:relative}
.section-title{font-size:16.5px;font-weight:600;padding-top:22px}
.tabs{display:flex;margin-top:17px;height:31px;font-size:11.5px}
.tab{display:flex;align-items:center;padding:0 17px;background:#e2e4e7;color:var(--ink-soft);border-radius:0 3px 3px 0}
.tab.on{background:var(--accent-btn);color:var(--white);border-radius:3px 0 0 3px}
.tab b{font-weight:600;margin-left:4px}
.views{position:absolute;right:71px;top:70px;display:flex;gap:17px}
.cards{display:flex;gap:19px;margin-top:20px}
.card{width:340px;height:167px;background:var(--white);border-radius:3px;position:relative;padding:21px;box-shadow:0 1px 2px rgba(0,0,0,.04)}
.menu{position:absolute;right:20px;top:21px}
.card-id{font-size:12px;color:var(--ink-soft);margin-top:1px}
.card-title{font-size:12px;color:var(--accent);margin-top:9px;font-weight:500}
.dates{display:flex;margin-top:14px}
.dates div{width:125px}
.label{font-size:9.5px;color:var(--ink-soft);letter-spacing:.2px}
.date{font-size:12px;color:var(--ink-soft);margin-top:5px}
.chips{display:flex;gap:7px;margin-top:17px}
.chip{height:24px;padding:0 9px;border-radius:12px;background:var(--chip);font-size:11px;color:var(--ink-soft);display:flex;align-items:center;gap:7px}
.tick{width:14px;height:14px;border-radius:50%;background:var(--tick);display:flex;align-items:center;justify-content:center}
</style>
</head>
<body>
<header class="hero">
  <div class="topbar">
    <div class="brand"><span class="brand-dot"></span>Corvantia</div>
    <nav class="nav"><a class="active" href="#">Assessments</a><a href="#">Colleagues</a><a href="#">Results</a></nav>
    <div class="tools">
      <svg width="18" height="18" viewBox="0 0 24 24" fill="none" stroke="#fff" stroke-width="1.6"><path d="M6 16V11a6 6 0 0 1 12 0v5l1.5 2h-15z"/><path d="M10 20a2 2 0 0 0 4 0"/></svg>
      <svg width="18" height="18" viewBox="0 0 24 24" fill="none" stroke="#fff" stroke-width="1.6"><circle cx="12" cy="12" r="3"/><path d="M12 2.5l2 2.3 3-.6.8 3 2.7 1.4-1.2 2.9 1.2 2.9-2.7 1.4-.8 3-3-.6-2 2.3-2-2.3-3 .6-.8-3-2.7-1.4 1.2-2.9-1.2-2.9 2.7-1.4.8-3 3 .6z"/></svg>
      <div class="avatar-sm" role="img" aria-label="User profile photo"></div>
    </div>
  </div>
  <div class="welcome">
    <div class="avatar-lg" role="img" aria-label="User profile photo"></div>
    <div class="greet">Welcome back!</div>
    <div class="user-name">Maya T. Santoso</div>
    <div class="create-btn">
      <svg width="13" height="13" viewBox="0 0 24 24" fill="none" stroke="#fff" stroke-width="2"><rect x="4" y="3" width="13" height="17" rx="1"/><path d="M8 8h5M8 12h3"/><circle cx="16" cy="16" r="3.5"/></svg>
      Create New Assessment
    </div>
  </div>
  <div class="summary-label">Summary</div>
  <div class="stats">
    <div class="stat">
      <div class="stat-icon"><svg width="22" height="22" viewBox="0 0 24 24" fill="none" stroke="#fff" stroke-width="1.5"><rect x="3" y="2.5" width="14" height="18" rx="1"/><path d="M6.5 7h7M6.5 11h4M6.5 15h3"/><circle cx="17" cy="17" r="3.5"/><path d="M15.5 17l1 1 2-2"/></svg></div>
      <div class="stat-num">7</div><div class="stat-title">My Assessments</div><div class="stat-sub">3 pending</div>
    </div>
    <div class="stat">
      <div class="stat-icon"><svg width="22" height="22" viewBox="0 0 24 24" fill="none" stroke="#fff" stroke-width="1.5"><path d="M12 2l1.5 3 3 .4-2.2 2 .6 3-2.9-1.5-2.9 1.5.6-3-2.2-2 3-.4z"/><path d="M3 13h3v8H3zM6 14h4l4 2h3a2 2 0 0 1 0 4H9"/><rect x="9" y="11" width="8" height="4"/></svg></div>
      <div class="stat-num">3</div><div class="stat-title">Endorsements</div><div class="stat-sub">1 pending</div>
    </div>
    <div class="stat">
      <div class="stat-icon"><svg width="22" height="22" viewBox="0 0 24 24" fill="none" stroke="#fff" stroke-width="1.5"><circle cx="7" cy="6" r="2.5"/><circle cx="17" cy="6" r="2.5"/><circle cx="12" cy="12" r="2.5"/><path d="M2 13a5 5 0 0 1 7-3M22 13a5 5 0 0 0-7-3M7 21a5 5 0 0 1 10 0"/></svg></div>
      <div class="stat-num">10</div><div class="stat-title">Colleagues</div><div class="stat-sub">Last updated on May 23, 2024</div>
    </div>
    <div class="stat">
      <div class="stat-icon"><svg width="22" height="22" viewBox="0 0 24 24" fill="none" stroke="#fff" stroke-width="1.5"><path d="M12 14V3M8 7l4-4 4 4"/><path d="M3 12v7a2 2 0 0 0 2 2h14a2 2 0 0 0 2-2v-7M3 14h5l1 2h6l1-2h5"/></svg></div>
      <div class="stat-num">7</div><div class="stat-title">Submissions</div><div class="stat-sub">Last submit on May 23, 2024</div>
    </div>
  </div>
</header>

<main class="main">
  <h2 class="section-title">Assessments</h2>
  <div class="tabs"><div class="tab on">Pending<b>3</b></div><div class="tab">Completed<b>4</b></div></div>
  <div class="views">
    <svg width="18" height="18" viewBox="0 0 24 24" fill="none" stroke="#0e78bb" stroke-width="1.8"><path d="M8 5h14M8 12h14M8 19h14M2 5h2M2 12h2M2 19h2"/></svg>
    <svg width="18" height="18" viewBox="0 0 24 24" fill="none" stroke="#8a8f96" stroke-width="1.6"><rect x="2" y="2" width="8" height="8"/><rect x="14" y="2" width="8" height="8"/><rect x="2" y="14" width="8" height="8"/><rect x="14" y="14" width="8" height="8"/></svg>
  </div>
  <div class="cards">
    <article class="card">
      <svg class="menu" width="4" height="16" viewBox="0 0 4 16" fill="#4b5057"><circle cx="2" cy="2" r="1.6"/><circle cx="2" cy="8" r="1.6"/><circle cx="2" cy="14" r="1.6"/></svg>
      <div class="card-id">1723091983</div>
      <div class="card-title">Application Design Capabilities</div>
      <div class="dates"><div><div class="label">PUBLISHED ON</div><div class="date">20/05/2024</div></div><div><div class="label">DUE DATE</div><div class="date">24/05/2024</div></div></div>
      <div class="chips"><span class="chip">Quiz</span><span class="chip">Endorsement</span><span class="chip">Submission</span></div>
    </article>
    <article class="card">
      <svg class="menu" width="4" height="16" viewBox="0 0 4 16" fill="#4b5057"><circle cx="2" cy="2" r="1.6"/><circle cx="2" cy="8" r="1.6"/><circle cx="2" cy="14" r="1.6"/></svg>
      <div class="card-id">1723091983</div>
      <div class="card-title">UI/UX Designer Assessments</div>
      <div class="dates"><div><div class="label">PUBLISHED ON</div><div class="date">20/05/2024</div></div><div><div class="label">DUE DATE</div><div class="date">24/05/2024</div></div></div>
      <div class="chips"><span class="chip">Quiz<span class="tick"><svg width="8" height="8" viewBox="0 0 10 10" fill="none" stroke="#fff" stroke-width="1.8"><path d="M2 5l2 2 4-4"/></svg></span></span><span class="chip">Endorsement</span></div>
    </article>
    <article class="card">
      <svg class="menu" width="4" height="16" viewBox="0 0 4 16" fill="#4b5057"><circle cx="2" cy="2" r="1.6"/><circle cx="2" cy="8" r="1.6"/><circle cx="2" cy="14" r="1.6"/></svg>
      <div class="card-id">1723091983</div>
      <div class="card-title">Sales Representative Assessments</div>
      <div class="dates"><div><div class="label">PUBLISHED ON</div><div class="date">20/05/2024</div></div><div><div class="label">DUE DATE</div><div class="date">24/05/2024</div></div></div>
      <div class="chips"><span class="chip">Quiz<span class="tick"><svg width="8" height="8" viewBox="0 0 10 10" fill="none" stroke="#fff" stroke-width="1.8"><path d="M2 5l2 2 4-4"/></svg></span></span><span class="chip">Endorsement<span class="tick"><svg width="8" height="8" viewBox="0 0 10 10" fill="none" stroke="#fff" stroke-width="1.8"><path d="M2 5l2 2 4-4"/></svg></span></span><span class="chip">Submission</span></div>
    </article>
  </div>
</main>
</body>
</html>
```